Defense contractor needs a roll-up for an exhibition

The booth we have booked has only a size of 3m².
So this will be the centerpiece of the whole booth.
We need a roll-up that attracts visitors and at the same time it should contain already designed graphics. These graphics are giving visitors an overview of our system. So it is necessary to have them exposed in a height that the booth personal can conveniently point with its fingers at them.
For information about our company and product visit:
https://www.brellowtrackline.com/
For designing you should use Adobe Illustrator and the templates provided in the zip file, to guarantee a perfect print.
I have supplied my business card that you can copy the logo. As the company logo will be already at the booth nearby the top of the roll-up, you should not place it there. It can be in the middle or at the bottom.
I have uploaded a picture of the booth. The roll up will be placed at the left of the screen and has a size of 80cm x 200cm

Defense

Defense

Serif

0054AA
0677BA
7BADD7
CADEEF
E8F1F8

• you must use the Adobe Illustrator template to have a good printing result
• company logo on the upper side of the roll-up

```html
<!DOCTYPE html>
<html lang="en">
<head>
<meta charset="utf-8">
<title>Brellow Trackline – Roll-up</title>
<link rel="stylesheet" href="https://fonts.googleapis.com/css2?family=Saira+Condensed:ital,wght@1,800&family=Archivo+Narrow:wght@700&family=Arimo:wght@400&display=swap">
<style>
  :root {
    --stage: #3c3c3e;
    --paper: #eef0f8;
    --ink: #0a0a0a;
    --white: #ffffff;
    --accent: #e87a1e;
    --shadow: #555558;
    --sky-top: #2a3f9a;
    --sky-mid: #7a7fd0;
    --sky-glow: #e8a6b8;
    --art-light: #f4f5fb;
    --art-tone: #c9cde6;
  }
  * { margin: 0; padding: 0; box-sizing: border-box; }
  html, body { width: 1200px; height: 2291px; overflow: hidden; background: var(--stage); }
  .rollup {
    position: absolute; left: 134px; top: 0;
    width: 932px; height: 2291px;
    background: var(--paper);
    border-top: 3px solid var(--accent);
    border-bottom: 3px solid var(--accent);
    overflow: hidden;
  }
  .hero-photo {
    position: absolute; left: 0; top: 0; width: 932px; height: 349px;
    background: linear-gradient(180deg, var(--sky-top) 0%, var(--sky-mid) 45%, var(--sky-glow) 75%, #1a1a2a 100%);
  }
  .banner-shape { position: absolute; left: 0; top: 349px; width: 932px; height: 610px; }
  .headline {
    position: absolute; left: 0; top: 425px; width: 932px;
    font-family: "Saira Condensed", "Arial Narrow", sans-serif;
    font-weight: 800; font-style: italic;
    font-size: 80px; line-height: 88px;
    color: var(--white); text-align: center; text-transform: uppercase;
    letter-spacing: 0.5px;
  }
  .brand-name {
    position: absolute; left: 81px; top: 996px;
    font-family: "Saira Condensed", "Arial Narrow", sans-serif;
    font-weight: 800; font-size: 66px; line-height: 70px;
    color: var(--ink); text-transform: uppercase;
  }
  .system-graphic {
    position: absolute; left: 22px; top: 1094px; width: 840px; height: 562px;
    background: radial-gradient(ellipse at 55% 55%, var(--art-light) 0%, var(--art-tone) 100%);
    border-radius: 6px;
  }
  .services { position: absolute; left: 90px; top: 1658px; width: 780px; color: var(--ink); }
  .services h2 {
    font-family: "Archivo Narrow", "Arial Narrow", sans-serif; font-weight: 700;
    font-size: 50px; line-height: 56px;
    display: inline-block; width: 282px; border-bottom: 4px solid var(--ink);
    padding-bottom: 2px;
  }
  .services .intro, .services .outro {
    font-family: "Archivo Narrow", "Arial Narrow", sans-serif; font-weight: 700;
    font-size: 30px; line-height: 40px;
  }
  .services .intro { margin-top: 12px; }
  .services ul { list-style: none; margin-top: 16px; }
  .services li {
    font-family: "Arimo", Arial, sans-serif; font-size: 32px; line-height: 40px;
    display: flex; align-items: center;
  }
  .services li svg { width: 30px; height: 30px; margin-right: 26px; flex: none; }
  .services .outro { margin-top: 18px; }
</style>
</head>
<body>
  <div class="rollup">
    <div class="hero-photo" role="img" aria-label="Battle tank silhouette against a colourful sunset sky above grass"></div>

    <svg class="banner-shape" viewBox="0 0 932 610" aria-hidden="true">
      <polygon points="0,429 0,480 559,601 932,480 932,429 559,555" fill="var(--shadow)"/>
      <polygon points="0,0 932,0 932,429 559,559 0,429" fill="var(--ink)"/>
    </svg>

    <h1 class="headline">Advanced combat<br>training systems for<br>realistic combat<br>simulation</h1>

    <div class="brand-name">Brellow Trackline</div>

    <div class="system-graphic" role="img" aria-label="System overview illustration: two tanks, three target stands and a command truck with monitors and instructors"></div>

    <section class="services">
      <h2>Services</h2>
      <p class="intro">The signature of the contract is not the end<br>it is just the beginning of a long-lasting partnership.<br>We offer</p>
      <ul>
        <li><svg viewBox="0 0 30 30"><circle cx="14" cy="16" r="11" fill="none" stroke="#0a0a0a" stroke-width="2.5"/><path d="M8 15 L13 20 L27 4" fill="none" stroke="#0a0a0a" stroke-width="3"/></svg>extended warranty programs</li>
        <li><svg viewBox="0 0 30 30"><circle cx="14" cy="16" r="11" fill="none" stroke="#0a0a0a" stroke-width="2.5"/><path d="M8 15 L13 20 L27 4" fill="none" stroke="#0a0a0a" stroke-width="3"/></svg>logistics support</li>
        <li><svg viewBox="0 0 30 30"><circle cx="14" cy="16" r="11" fill="none" stroke="#0a0a0a" stroke-width="2.5"/><path d="M8 15 L13 20 L27 4" fill="none" stroke="#0a0a0a" stroke-width="3"/></svg>maintenance contracts</li>
        <li><svg viewBox="0 0 30 30"><circle cx="14" cy="16" r="11" fill="none" stroke="#0a0a0a" stroke-width="2.5"/><path d="M8 15 L13 20 L27 4" fill="none" stroke="#0a0a0a" stroke-width="3"/></svg>long-term spare part services</li>
      </ul>
      <p class="outro">to keep the equipment in perfect operational condition</p>
    </section>
  </div>
</body>
</html>
```